Meridale Bed Company Needs Business Card

Looking for a very nice looking business card. Creative but not extravagant. We sell beds and pillows across the U.S. and need something professional but catchy. I have attached the logo.

Name : Devin Holt
Title : President
Phone : (800) 471-2960
Email: sleep@quilmora.com
Website: www.quilmora.com

Can be single-sided or double-sided
horizontal or vertical

Can use Blues/Greys

Target Market(s)

Mass Market

Industry/Entity Type

Retail

Contact Information for Business Card

Name : Devin Holt
Title : President
Phone : (800) 471-2960
Email: sleep@quilmora.com
Website: www.quilmora.com

Requirements
Must have
• Clean, Modern, Smooth
• Can use Blues/Greys
• On the other side without the information - have something simple like www.quilmora.com or our logo
Nice to have
• Surprise me
Should not have
• Nothing crazy, nothing cluttered

```html
<!DOCTYPE html>
<html lang="en">
<head>
<meta charset="utf-8">
<title>Quilmora Business Card</title>
<link href="https://fonts.googleapis.com/css2?family=Open+Sans:wght@400;600;700&display=swap" rel="stylesheet">
<style>
  :root {
    --stage: #000000;
    --card-blue: #36a7da;
    --pattern-blue: #2f9ccf;
    --ink-white: #ffffff;
  }
  * { margin: 0; padding: 0; box-sizing: border-box; }
  html, body { width: 1200px; height: 900px; overflow: hidden; background: var(--stage); }
  .canvas { position: relative; width: 1200px; height: 900px; }

  .card {
    position: absolute;
    top: 275px;
    width: 477px;
    height: 293px;
    background: var(--card-blue);
    overflow: hidden;
    color: var(--ink-white);
  }
  .card--front { left: 116px; border-radius: 0 62px 0 62px; }
  .card--back { left: 622px; top: 276px; height: 292px; border-radius: 62px 0 62px 0; }

  .pattern-area {
    position: absolute;
    inset: 0;
    background: linear-gradient(180deg, var(--card-blue) 0%, var(--pattern-blue) 50%, var(--card-blue) 100%);
  }

  .brand-name {
    position: absolute;
    font-family: "Open Sans", sans-serif;
    font-weight: 400;
    line-height: 1;
    color: var(--ink-white);
    white-space: nowrap;
  }
  .card--front .brand-name { left: 34px; top: 94px; font-size: 60px; }
  .card--back .brand-name { left: 0; right: 0; text-align: center; top: 114px; font-size: 54px; }

  .identity {
    position: absolute;
    right: 19px;
    top: 30px;
    text-align: right;
    font-family: "Open Sans", sans-serif;
  }
  .identity__name { font-weight: 700; font-size: 19px; line-height: 22px; }
  .identity__title { font-weight: 400; font-size: 14.5px; line-height: 18px; }

  .contact {
    position: absolute;
    right: 20px;
    top: 195px;
    list-style: none;
    font-family: "Open Sans", sans-serif;
    font-size: 13px;
  }
  .contact__item {
    display: flex;
    justify-content: flex-end;
    align-items: center;
    gap: 7px;
    height: 20px;
  }
  .contact__icon { width: 11px; height: 11px; flex: none; }

  .web-rule {
    position: absolute;
    left: 0;
    right: 0;
    top: 218px;
    display: flex;
    align-items: center;
    gap: 10px;
    font-family: "Open Sans", sans-serif;
    font-weight: 600;
    font-size: 11.5px;
    letter-spacing: 2.6px;
  }
  .web-rule__line { flex: 1; height: 1.5px; background: var(--ink-white); }
  .web-rule__line--left { flex: 0 0 156px; }
</style>
</head>
<body>
<main class="canvas">

  <section class="card card--front" aria-label="Business card front">
    <div class="pattern-area" role="img" aria-label="Faint repeating brand pattern background"></div>
    <div class="identity">
      <p class="identity__name">Devin Holt</p>
      <p class="identity__title">President</p>
    </div>
    <p class="brand-name">quilmora</p>
    <ul class="contact">
      <li class="contact__item">(800) 471-2960
        <svg class="contact__icon" viewBox="0 0 12 12" aria-hidden="true"><path fill="#fff" d="M2.6 1 4.3 2.8 3.4 4.2c.8 1.7 2.2 3.2 4 4l1.4-.9L10.6 9 9.4 10.8C5 10.6 1.4 7 1.2 2.6Z"/></svg>
      </li>
      <li class="contact__item">sleep@quilmora.com
        <svg class="contact__icon" viewBox="0 0 12 12" aria-hidden="true"><rect x="0.5" y="2.5" width="11" height="7.5" fill="#fff"/><path d="M0.8 3 6 7 11.2 3" fill="none" stroke="#36a7da" stroke-width="1"/></svg>
      </li>
      <li class="contact__item">www.quilmora.com
        <svg class="contact__icon" viewBox="0 0 12 12" aria-hidden="true"><circle cx="6" cy="6" r="5.5" fill="#fff"/><path d="M0.8 6h10.4M6 0.7c-2.4 2.8-2.4 7.8 0 10.6M6 0.7c2.4 2.8 2.4 7.8 0 10.6" fill="none" stroke="#36a7da" stroke-width="0.9"/></svg>
      </li>
    </ul>
  </section>

  <section class="card card--back" aria-label="Business card back">
    <div class="pattern-area" role="img" aria-label="Faint repeating brand pattern background"></div>
    <p class="brand-name">quilmora</p>
    <div class="web-rule">
      <span class="web-rule__line web-rule__line--left"></span>
      <span class="web-rule__text">www.quilmora.com</span>
      <span class="web-rule__line"></span>
    </div>
  </section>

</main>
</body>
</html>
```